Business Card Design Project for a Restaurant/Wine Bar

New, fresh business card design for Brevenna Wine Bar & Restaurant, Bandon, Oregon. We are an established restaurant on the Oregon coast featuring "Italian coastal cuisine."

"Brevenna" means bay leaf in Italian. We aren't sure if we would like our logo on the card or not, but if you have something interesting that uses it, then please do so. The basic information is essential - full restaurant name, address, phone and website (do not use www). The font on our menu and wine list may give you some sort of an idea of our style.

One-sided card needed as we often use the backside to write down various types of info for customers.
Updates

After seeing a few submissions, we would like to see what designers can come up with-using the logo, just the leaf, or none at all. Sky is the limit as long as our full restaurant name, address, phone and website (please leave out www) are there. Please contact us if questions!

I appreciate all of your designs! Our deadline is next week, but I will continue to give feedback on designs as I can. This is our busiest season, so my co-owner/chef/husband, won't have time to look at the designs for awhile. When he does, we can make our decision.

cheers,
Maren

Target Market(s)

Fine dining/wine crowd. Would like something simple and elegant, but not pretentious or stuffy. Brevenna means bay laurel (bay leaf) in Italian (please see our logo).

Industry/Entity Type

Restaurant

Requirements
Must have
• Full Name of Restaurant: Brevenna Wine Bar & Restaurant
Address: 812 4th Ave NW, Calder Bay, Cascadia 00000
Phone: 541.555.0172
website: brevennawinebar.example (do not use www)
Should not have
• Loud colors.

```html
<!DOCTYPE html>
<html lang="en">
<head>
<meta charset="utf-8">
<title>Brevenna Wine Bar &amp; Restaurant — Business Card</title>
<link rel="stylesheet" href="https://fonts.googleapis.com/css2?family=Old+Standard+TT:wght@400;700&display=swap">
<style>
  :root {
    --backdrop: #d8d4ca;
    --card: #e4e7dd;
    --gold: #a68f57;
    --sage-ink: #7b8670;
    --sage-line: #8d9c7e;
    --band: #b9a772;
  }
  * { box-sizing: border-box; margin: 0; padding: 0; }
  html, body {
    width: 1200px; height: 1023px; overflow: hidden;
    background: var(--backdrop);
  }
  body {
    display: flex; align-items: center; justify-content: center;
    font-family: "Old Standard TT", Georgia, serif;
  }
  .card {
    position: relative;
    width: 500px; height: 875px;
    background: var(--card);
    box-shadow: 0 6px 24px rgba(60, 50, 30, 0.18);
    display: flex; flex-direction: column; align-items: center;
    text-align: center;
    overflow: hidden;
  }
  .wordmark {
    margin-top: 110px;
    color: var(--gold);
    font-weight: 700;
    text-transform: uppercase;
    line-height: 1.05;
  }
  .wordmark .primary { display: block; font-size: 62px; letter-spacing: 3px; }
  .wordmark .secondary { display: block; font-size: 46px; letter-spacing: 4px; }
  .business-name {
    margin-top: 90px;
    color: var(--gold);
    font-size: 30px; font-weight: 700; letter-spacing: 2px;
    text-transform: uppercase;
  }
  .business-type {
    margin-top: 4px;
    color: var(--sage-ink);
    font-size: 20px; font-weight: 700;
    font-variant: small-caps; letter-spacing: 1px;
  }
  .contact { margin-top: 38px; }
  .contact dt {
    color: var(--sage-ink);
    font-size: 15px; font-weight: 700; letter-spacing: 1.5px;
    text-transform: uppercase;
    margin-top: 20px;
  }
  .contact dt:first-child { margin-top: 0; }
  .contact dd {
    color: var(--gold);
    font-size: 27px; line-height: 1.2;
    margin-top: 4px;
  }
  .contact sup { font-size: 15px; }
  .edge-band {
    position: absolute; left: 0; right: 0; bottom: 0;
    height: 52px;
    background: var(--band);
    border-top: 5px solid var(--sage-line);
  }
</style>
</head>
<body>
  <article class="card" aria-label="Brevenna Wine Bar &amp; Restaurant business card">
    <div class="wordmark">
      <span class="primary">Brevenna</span>
      <span class="secondary">Wine Bar</span>
    </div>

    <h1 class="business-name">Brevenna</h1>
    <p class="business-type">Wine Bar &amp; Restaurant</p>

    <dl class="contact">
      <dt>Address</dt>
      <dd>812 4<sup>th</sup> Ave NW, Calder Bay,<br>Cascadia 00000</dd>
      <dt>Phone</dt>
      <dd>541.555.0172</dd>
      <dt>Website</dt>
      <dd>brevennawinebar.example</dd>
    </dl>

    <div class="edge-band"></div>
  </article>
</body>
</html>
```